****Business Card Design for Quarrystone Development. Design based around attached logo/company name

I’m looking for business card design for my company Quarrystone Development Group,LLC. Design should be professional, sharp and minimal. Outside of the attached logos, greyscale colors for remainder of cards. My thoughts are two-sided card with attached logo on one side and my info on the other but open to one-sided as well with right design.
Target Market(s)
Real estate professionals including banks, private investors, property owners, developers, commercial tenants like Brewlantern, Grovika or Tanquist’s.
Industry/Entity Type
Commercial real estate development and investments.
Contact Information for Business Card
Name, title, email, phone #’s, web address and physical address
Font styles to use
Other font styles liked:
- Helvetica, Garamond, etc
Colors
Designer to choose only greyscale colors for use in the design.
Requirements
Must have
- Attached logo first or second options.
Nice to have
- Two sided card with logo on one side. Attached Logo/company name can be laid out any way that flows as long as it’s legible.name
Should not have
- No loud colors. ***Please do not include logo, I have removed the company design with a logo image.

```html
<!DOCTYPE html>
<html lang="en">
<head>
<meta charset="UTF-8">
<title>Quarrystone Development – Business Card</title>
<link rel="stylesheet" href="https://fonts.googleapis.com/css2?family=EB+Garamond:wght@400;600&family=Arimo:wght@400&display=swap">
<style>
  :root {
    --page-bg: #d9d4cc;
    --card-top: #eeece8;
    --card-bottom: #dcd9d4;
    --card-edge: #f6f5f2;
    --ink-dark: #4a4d55;
    --ink-mid: #5b5d62;
    --band-start: #8c8985;
    --band-end: rgba(140, 137, 133, 0);
    --band-text: #f4f2ee;
  }
  * { margin: 0; padding: 0; box-sizing: border-box; }
  html, body {
    width: 1200px;
    height: 897px;
    overflow: hidden;
    background: var(--page-bg);
  }
  .card {
    position: absolute;
    left: 175px;
    top: 229px;
    width: 895px;
    height: 484px;
    border-radius: 22px;
    background: linear-gradient(160deg, var(--card-top), var(--card-bottom));
    border: 1px solid var(--card-edge);
    box-shadow: 0 6px 22px rgba(0, 0, 0, 0.12);
    overflow: hidden;
  }
  .wordmark {
    position: absolute;
    left: 51px;
    top: 58px;
    font-family: "EB Garamond", Garamond, serif;
    font-weight: 400;
    color: var(--ink-dark);
  }
  .wordmark-name {
    display: block;
    font-size: 46px;
    line-height: 1;
    letter-spacing: 1.5px;
  }
  .wordmark-sub {
    display: block;
    margin-top: 8px;
    font-size: 17px;
    letter-spacing: 2.6px;
  }
  .name-band {
    position: absolute;
    left: 0;
    top: 186px;
    width: 600px;
    height: 69px;
    background: linear-gradient(90deg, var(--band-start) 0%, var(--band-start) 55%, var(--band-end) 100%);
    padding: 10px 0 0 51px;
    color: var(--band-text);
  }
  .person-name {
    font-family: "EB Garamond", Garamond, serif;
    font-weight: 600;
    font-size: 24px;
    letter-spacing: 0.6px;
    line-height: 1.05;
  }
  .person-title {
    font-family: "Arimo", Helvetica, Arial, sans-serif;
    font-size: 18px;
    line-height: 1.3;
  }
  .contact {
    position: absolute;
    left: 49px;
    top: 285px;
    font-family: "Arimo", Helvetica, Arial, sans-serif;
    font-size: 18.5px;
    color: var(--ink-mid);
  }
  .address { line-height: 25px; margin-bottom: 22px; }
  .contact-line {
    display: flex;
    align-items: center;
    gap: 10px;
    height: 30px;
  }
  .contact-line svg { width: 15px; height: 15px; fill: var(--ink-mid); flex: none; }
</style>
</head>
<body>
  <div class="card">
    <div class="wordmark">
      <span class="wordmark-name">QUARRYSTONE</span>
      <span class="wordmark-sub">DEVELOPMENT GROUP, LLC</span>
    </div>

    <div class="name-band">
      <p class="person-name">DANIEL OSTRANDER</p>
      <p class="person-title">Founder/CEO</p>
    </div>

    <div class="contact">
      <p class="address">2150 Ledgewood Avenue<br>Fairhaven AB 7841</p>
      <p class="contact-line">
        <svg viewBox="0 0 24 24" aria-hidden="true"><path d="M6.6 10.8a15.1 15.1 0 0 0 6.6 6.6l2.2-2.2a1 1 0 0 1 1-.25 11.4 11.4 0 0 0 3.6.57 1 1 0 0 1 1 1V20a1 1 0 0 1-1 1A17 17 0 0 1 3 4a1 1 0 0 1 1-1h3.5a1 1 0 0 1 1 1c0 1.25.2 2.45.57 3.57a1 1 0 0 1-.25 1z"/></svg>
        (555)-214-0396
      </p>
      <p class="contact-line">
        <svg viewBox="0 0 24 24" aria-hidden="true"><path d="M2 5h20v14H2z M2 5l10 8 10-8" fill="none" stroke="#5b5d62" stroke-width="0"/><path d="M2 6.5V19h20V6.5l-10 7.5z"/><path d="M2 5h20l-10 7.3z"/></svg>
        info@quarrystonedevelopment.com
      </p>
      <p class="contact-line">
        <svg viewBox="0 0 24 24" aria-hidden="true"><path d="M12 2a10 10 0 1 0 0 20 10 10 0 0 0 0-20zm0 2c1.1 0 2.4 2.1 2.9 5H9.1C9.6 6.1 10.9 4 12 4zM4.3 10h3.1a17 17 0 0 0 0 4H4.3a8 8 0 0 1 0-4zm4.8 5h5.8c-.5 2.9-1.8 5-2.9 5s-2.4-2.1-2.9-5zm7.5-1a17 17 0 0 0 0-4h3.1a8 8 0 0 1 0 4z"/></svg>
        www.quarrystonedevelopment.com
      </p>
    </div>
  </div>
</body>
</html>
```